Stonebridge Building and Projects business cards

A business card with watermark background (construction work)

Company logo attached

Home improvement projects
House renovations
Bathroom and kitchen renovations
House extensions
New builds and granny flats

Director Omar Haddani
(Phone number)
omar@sbpbuilding.com.au
(Instagram logo) sbp_building

```html
<!DOCTYPE html>
<html lang="en">
<head>
<meta charset="utf-8">
<title>Stonebridge Building and Projects – Business Cards</title>
<link rel="stylesheet" href="https://fonts.googleapis.com/css2?family=Questrial&family=Source+Sans+3:wght@400&display=swap">
<style>
  :root {
    --backdrop: #2f2f2f;
    --card-light: #f7f7f7;
    --card-mid: #e6e6e6;
    --card-low: #d9d9d9;
    --brand-blue: #2f7bbf;
    --text-grey: #4d4d4d;
    --text-dark: #3a3a3a;
    --rule-grey: #555555;
  }
  * { box-sizing: border-box; margin: 0; padding: 0; }
  html, body { width: 1200px; height: 624px; overflow: hidden; }
  body { background: var(--backdrop); position: relative; }

  .card {
    position: absolute;
    top: 176px;
    width: 476px;
    height: 285px;
    overflow: hidden;
    box-shadow: 0 6px 18px rgba(0,0,0,0.45);
  }
  .card--services { left: 100px; }
  .card--contact { left: 624px; }

  .card__watermark {
    position: absolute;
    inset: 0;
    background: linear-gradient(180deg, var(--card-light) 0%, var(--card-light) 45%, var(--card-mid) 80%, var(--card-low) 100%);
  }

  /* Services side */
  .service {
    position: absolute;
    font-family: "Source Sans 3", sans-serif;
    font-size: 10.6px;
    color: var(--text-grey);
    white-space: nowrap;
    line-height: 1;
  }
  .service__tick {
    position: absolute;
    left: -20px;
    top: 0;
    width: 9px;
    height: 9px;
  }

  /* Contact side */
  .brand {
    position: absolute;
    left: 45px;
    top: 100px;
    width: 160px;
    text-align: center;
    font-family: "Questrial", sans-serif;
    color: var(--brand-blue);
  }
  .brand__mark {
    width: 30px;
    height: 30px;
    background: var(--brand-blue);
    margin: 0 auto 10px;
  }
  .brand__name {
    font-size: 14px;
    line-height: 1.25;
  }
  .divider {
    position: absolute;
    left: 205px;
    top: 81px;
    width: 1px;
    height: 123px;
    background: var(--rule-grey);
  }
  .person {
    position: absolute;
    left: 219px;
    top: 90px;
    font-family: "Questrial", sans-serif;
  }
  .person__name {
    font-size: 22px;
    color: var(--brand-blue);
    line-height: 1;
    font-weight: 400;
  }
  .person__role {
    margin-top: 6px;
    font-size: 12.5px;
    color: var(--text-dark);
  }
  .contacts {
    position: absolute;
    left: 219px;
    top: 140px;
    list-style: none;
    font-family: "Questrial", sans-serif;
    font-size: 13px;
    color: var(--text-dark);
  }
  .contacts__item {
    display: flex;
    align-items: center;
    height: 19.5px;
  }
  .contacts__icon {
    width: 11px;
    height: 11px;
    margin-right: 7px;
    flex: none;
  }
</style>
</head>
<body>

  <section class="card card--services">
    <div class="card__watermark" role="img" aria-label="Faded photograph of a construction site with cranes and workers"></div>

    <p class="service" style="left:73px; top:114px;">
      <svg class="service__tick" viewBox="0 0 10 10"><path d="M1 5.5 L4 8.5 L9 1.5" fill="none" stroke="#2f7bbf" stroke-width="1.4"/></svg>
      Home improvement projects
    </p>
    <p class="service" style="left:260px; top:114px;">
      <svg class="service__tick" viewBox="0 0 10 10"><path d="M1 5.5 L4 8.5 L9 1.5" fill="none" stroke="#2f7bbf" stroke-width="1.4"/></svg>
      Bathroom and kitchen renovations
    </p>
    <p class="service" style="left:73px; top:136px;">
      <svg class="service__tick" viewBox="0 0 10 10"><path d="M1 5.5 L4 8.5 L9 1.5" fill="none" stroke="#2f7bbf" stroke-width="1.4"/></svg>
      House renovations
    </p>
    <p class="service" style="left:260px; top:136px;">
      <svg class="service__tick" viewBox="0 0 10 10"><path d="M1 5.5 L4 8.5 L9 1.5" fill="none" stroke="#2f7bbf" stroke-width="1.4"/></svg>
      House extensions
    </p>
    <p class="service" style="left:183px; top:162px;">
      <svg class="service__tick" viewBox="0 0 10 10"><path d="M1 5.5 L4 8.5 L9 1.5" fill="none" stroke="#2f7bbf" stroke-width="1.4"/></svg>
      New builds and granny flats
    </p>
  </section>

  <section class="card card--contact">
    <div class="card__watermark" role="img" aria-label="Faded photograph of a construction worker in a hard hat with a crane behind"></div>

    <div class="brand">
      <div class="brand__mark"></div>
      <p class="brand__name">Stonebridge<br>Building and Projects</p>
    </div>

    <div class="divider"></div>

    <div class="person">
      <h1 class="person__name">Omar Haddani</h1>
      <p class="person__role">Director</p>
    </div>

    <ul class="contacts">
      <li class="contacts__item">
        <svg class="contacts__icon" viewBox="0 0 12 12"><circle cx="6" cy="6" r="6" fill="#2f7bbf"/><path d="M4 3 L5 3.2 L5.5 4.8 L4.8 5.3 Q5.5 6.6 6.7 7.2 L7.2 6.5 L8.8 7 L9 8 Q8.5 9 7.5 9 Q4.5 8.5 3 4.5 Q3 3.5 4 3 Z" fill="#fff"/></svg>
        111-555-777
      </li>
      <li class="contacts__item">
        <svg class="contacts__icon" viewBox="0 0 12 12"><circle cx="6" cy="6" r="6" fill="#2f7bbf"/><rect x="3" y="4" width="6" height="4.2" fill="#fff"/><path d="M3 4 L6 6.4 L9 4" fill="none" stroke="#2f7bbf" stroke-width="0.8"/></svg>
        omar@sbpbuilding.com.au
      </li>
      <li class="contacts__item">
        <svg class="contacts__icon" viewBox="0 0 12 12"><circle cx="6" cy="6" r="6" fill="#2f7bbf"/></svg>
        sbp_building
      </li>
    </ul>
  </section>

</body>
</html>
```